Corporate Travel Technology Company needs new Business Card design

We need a new business card design to reflect our re-branded company. Our company is called tolvEn (pronounced tolvenn) and we provide Business Intelligence and mobile travel management solutions for the corporate travel industry. Our multinational customers use our solutions to manage large travel budgets and frequent travellers, as well as to save money and reduce risk. We'd like to see designs that use the blue and green palette as well as our corporate logo (attached below). The design should communicate innovation, insight, forward thinking, contemporary, trusted.

Target Market(s)

Large multinational corporates and Travel Agencies.

Industry/Entity Type

Business

Contact Information for Business Card

Rosalind Mercer
Chief Executive
tolvEn
Phone number - +61 (0)2 8134 2907
Email address - rosalind.mercer@tolven-example.com
Mobile number - +61 (0)438 516 702
www.tolven-example.com

Font styles to use
Other font styles liked:
• Please use font as close to corporate logo as possible

Colors
0255a3
0393ce
00a990
33b8a4
33a6d7
3176b5

Requirements
Must have
• Please include the words;
• Mobile Travel Management
• Accelerating Travel Business Insights
• Use corporate logo - although icon can be stylised if needed

```html
<!DOCTYPE html>
<html lang="en">
<head>
<meta charset="utf-8">
<title>Tolven business card</title>
<link href="https://fonts.googleapis.com/css2?family=Open+Sans:wght@400;600;700&display=swap" rel="stylesheet">
<style>
  :root {
    --stage: #e9ecee;
    --white: #ffffff;
    --slate-top: #95a3a3;
    --slate-bottom: #3a4547;
    --sky-top: #5fcdf2;
    --sky-bottom: #0a78c8;
    --brand-blue: #33a6d7;
    --title-blue: #5cc4f0;
    --card-shadow: rgba(0, 0, 0, 0.18);
  }
  * { box-sizing: border-box; margin: 0; padding: 0; }
  html, body {
    width: 1200px;
    height: 913px;
    overflow: hidden;
    background: var(--stage);
    font-family: "Open Sans", Arial, sans-serif;
  }
  .stage {
    position: relative;
    width: 1200px;
    height: 913px;
  }
  .card {
    position: absolute;
    top: 306px;
    width: 520px;
    height: 300px;
    border-radius: 18px;
    overflow: hidden;
    box-shadow: 0 10px 28px var(--card-shadow);
  }

  /* Front: contact side */
  .card-front {
    left: 45px;
    background: var(--white);
  }
  .contact-panel {
    position: absolute;
    top: 0;
    right: 0;
    width: 64%;
    height: 100%;
    background: linear-gradient(170deg, var(--slate-top) 0%, var(--slate-bottom) 100%);
    clip-path: polygon(12% 0, 100% 0, 100% 100%, 0 100%);
  }
  .contact-block {
    position: absolute;
    top: 38px;
    right: 30px;
    text-align: right;
    color: var(--white);
  }
  .person-name {
    font-size: 23px;
    font-weight: 700;
    line-height: 1.15;
  }
  .person-title {
    font-size: 13px;
    font-weight: 400;
    line-height: 1.3;
    color: var(--title-blue);
    margin-bottom: 30px;
  }
  .contact-list { list-style: none; }
  .contact-item {
    display: flex;
    justify-content: flex-end;
    align-items: center;
    gap: 7px;
    font-size: 12.5px;
    line-height: 20px;
  }
  .contact-icon {
    width: 11px;
    height: 11px;
    flex: none;
  }

  /* Back: brand side */
  .card-back {
    left: 635px;
    background: linear-gradient(165deg, var(--sky-top) 0%, var(--sky-bottom) 100%);
  }
  .brand-name {
    position: absolute;
    top: 78px;
    left: 0;
    width: 100%;
    text-align: center;
    font-size: 70px;
    font-weight: 600;
    letter-spacing: 2px;
    color: var(--white);
    line-height: 1;
  }
  .tagline-list {
    position: absolute;
    left: 150px;
    top: 200px;
    list-style: none;
    color: var(--white);
  }
  .tagline {
    display: flex;
    align-items: center;
    gap: 8px;
    font-size: 14px;
    line-height: 22px;
  }
  .tagline-arrow {
    width: 10px;
    height: 10px;
    flex: none;
  }
</style>
</head>
<body>
<main class="stage">

  <section class="card card-front" aria-label="Business card front">
    <div class="contact-panel"></div>
    <div class="contact-block">
      <p class="person-name">Rosalind Mercer</p>
      <p class="person-title">Chief Executive</p>
      <ul class="contact-list">
        <li class="contact-item">+61 (0)438 516 702
          <svg class="contact-icon" viewBox="0 0 12 12" aria-hidden="true"><rect x="3" y="0.5" width="6" height="11" rx="1.2" fill="none" stroke="#33a6d7" stroke-width="1.2"/></svg>
        </li>
        <li class="contact-item">+61 (0)2 8134 2907
          <svg class="contact-icon" viewBox="0 0 12 12" aria-hidden="true"><path d="M2.5 1 L4.5 1 L5.5 3.5 L4.2 4.6 C5 6.3 5.8 7.1 7.4 7.8 L8.5 6.5 L11 7.5 L11 9.5 C11 10.3 10.3 11 9.5 11 C5 10.6 1.4 7 1 2.5 C1 1.7 1.7 1 2.5 1 Z" fill="#33a6d7"/></svg>
        </li>
        <li class="contact-item">www.tolven-example.com
          <svg class="contact-icon" viewBox="0 0 12 12" aria-hidden="true"><circle cx="6" cy="6" r="5" fill="none" stroke="#33a6d7" stroke-width="1.2"/><ellipse cx="6" cy="6" rx="2.2" ry="5" fill="none" stroke="#33a6d7" stroke-width="1"/><line x1="1" y1="6" x2="11" y2="6" stroke="#33a6d7" stroke-width="1"/></svg>
        </li>
        <li class="contact-item">rosalind.mercer@tolven-example.com
          <svg class="contact-icon" viewBox="0 0 12 12" aria-hidden="true"><rect x="0.8" y="2.5" width="10.4" height="7" rx="1" fill="none" stroke="#33a6d7" stroke-width="1.2"/><polyline points="1,3 6,7 11,3" fill="none" stroke="#33a6d7" stroke-width="1.1"/></svg>
        </li>
      </ul>
    </div>
  </section>

  <section class="card card-back" aria-label="Business card back">
    <p class="brand-name">Tolven</p>
    <ul class="tagline-list">
      <li class="tagline">
        <svg class="tagline-arrow" viewBox="0 0 10 10" aria-hidden="true"><polygon points="1,1 9,5 1,9" fill="none" stroke="#ffffff" stroke-width="1.2"/></svg>
        Mobile Travel Management
      </li>
      <li class="tagline">
        <svg class="tagline-arrow" viewBox="0 0 10 10" aria-hidden="true"><polygon points="1,1 9,5 1,9" fill="none" stroke="#ffffff" stroke-width="1.2"/></svg>
        Accelerating Travel Business Insights
      </li>
    </ul>
  </section>

</main>
</body>
</html>
```